KPL Construction we build lodges in Botswana

We need a Design Layout only with Categories where we can update each projects photos.... We have a web address and a host - kpl.construction

```html
<!DOCTYPE html>
<html lang="en">
<head>
<meta charset="utf-8">
<title>KPL Construction – Single Post View</title>
<link href="https://fonts.googleapis.com/css2?family=Open+Sans:ital,wght@0,400;0,600;0,700;1,400&family=Raleway:wght@200;300;600;700&family=Oswald:wght@500;700&display=swap" rel="stylesheet">
<style>
:root{
  --ink:#222;
  --muted:#777;
  --page:#f3f3f3;
  --dark:#1d1d1d;
  --teal:#4f9a98;
  --red:#e0251b;
  --blue:#1f6fd0;
  --line:#d6d6d6;
  --white:#fff;
}
*{box-sizing:border-box;margin:0;padding:0}
html,body{width:1200px;height:3070px;overflow:hidden}
body{position:relative;background:var(--page);font-family:"Open Sans",Arial,sans-serif;color:var(--ink);font-size:13.5px;line-height:21px}
.abs{position:absolute}

/* hero */
.hero-photo{left:0;top:0;width:1200px;height:620px;background:linear-gradient(180deg,#6f6f6f 0%,#9a9a9a 35%,#6a6a6a 70%,#2a2a2a 100%)}
.nav-bar{left:0;top:0;width:1200px;height:100px;background:rgba(255,255,255,.35)}
.brand{left:14px;top:30px;display:flex;align-items:center;gap:10px;font-family:"Raleway",sans-serif;font-weight:700;font-size:18px;color:#111;letter-spacing:1px}
.brand-dot{width:22px;height:22px;border-radius:50%;background:#111}
.nav{left:606px;top:32px;display:flex;gap:0;font-family:"Raleway",sans-serif;font-weight:700;font-size:11px;color:#222}
.nav a{display:block;padding:14px 18px;color:inherit;text-decoration:none}
.nav a.active{background:var(--teal);color:#fff}
.cart{left:1068px;top:30px;display:flex;align-items:center;gap:12px;font-family:"Raleway",sans-serif;font-weight:700;font-size:11px}
.cart-ring{width:40px;height:40px;border-radius:50%;border:2px solid #222;display:flex;align-items:center;justify-content:center}
.hero-title{left:0;top:165px;width:1200px;text-align:center;font-family:"Raleway",sans-serif;font-weight:200;color:rgba(255,255,255,.9);font-size:68px;line-height:78px;letter-spacing:12px}
.hero-sub{left:420px;top:318px;width:360px;text-align:center;color:rgba(255,255,255,.85);font-size:14px;line-height:20px}
.btn-start{left:536px;top:410px;width:124px;height:36px;background:var(--teal);color:#fff;font-family:"Raleway",sans-serif;font-weight:700;font-size:10px;letter-spacing:1px;display:flex;align-items:center;justify-content:center}

/* dark band */
.dark-band{left:0;top:600px;width:1200px;height:510px;background:linear-gradient(180deg,#1b1b1b 0%,#2a2a2a 60%,#555 100%)}
.page-title{left:0;top:622px;width:1200px;text-align:center;font-family:"Raleway",sans-serif;font-weight:700;font-size:32px;color:#fff;line-height:44px}

.date-badge{left:76px;top:690px;width:71px}
.date-badge .top{background:var(--red);color:#fff;text-align:center;font-family:"Oswald",sans-serif;font-weight:700;font-size:18px;line-height:22px;padding:6px 0}
.date-badge .year{background:#fff;color:#222;text-align:center;font-family:"Oswald",sans-serif;font-weight:700;font-size:15px;line-height:24px}

.slider{left:164px;top:690px;width:680px;height:303px;background:linear-gradient(90deg,#2f7fd6 0 30px,transparent 30px calc(100% - 30px),#2f7fd6 calc(100% - 30px))}
.slide-photo{left:30px;top:0;width:620px;height:303px;background:linear-gradient(180deg,#b7b2a8 0%,#8d877c 45%,#4a4640 100%)}
.slide-caption{left:30px;top:205px;width:620px;height:98px;background:rgba(0,0,0,.55);color:#fff;padding:14px 20px}
.slide-caption h3{font-family:"Raleway",sans-serif;font-weight:700;font-size:19px;line-height:26px}
.slide-caption p{font-size:10.5px;line-height:15px;margin-top:6px}
.slide-arrow{top:138px;width:20px;height:28px}

.meta{left:164px;top:993px;width:680px;height:20px;display:flex;align-items:center;font-size:11px;color:#bbb}
.meta span{display:flex;align-items:center;gap:8px;width:110px}
.meta .author{color:var(--red)}

.post{left:164px;top:1022px;width:680px}
.post h1{font-family:"Oswald",sans-serif;font-weight:700;font-size:22px;color:#fff;line-height:30px}
.post .lead{font-weight:700;color:#fff;font-size:12.5px;line-height:18px}
.post p{margin:0}
.post .body{color:#333;font-size:12.5px;line-height:20px}
.post blockquote{margin:4px 0 4px 30px;padding-left:12px;border-left:3px solid var(--red);color:var(--red);font-style:italic;font-size:12.5px;line-height:20px}
.rule{left:78px;top:1436px;width:766px;height:1px;background:var(--line)}

/* sidebar */
.sidebar{left:864px;top:690px;width:244px;color:#fff}
.side-h{font-family:"Raleway",sans-serif;font-weight:700;font-size:11px;letter-spacing:.5px;line-height:16px}
.side-about{font-size:12px;line-height:18px;font-weight:600;margin-top:10px}
.cats{margin-top:16px;list-style:none}
.cats li{display:flex;align-items:center;gap:10px;font-size:12px;height:35px;border-bottom:1px solid rgba(255,255,255,.6)}
.cats li i{width:12px;height:12px;border:1px solid #ddd;display:block}
.recent{left:864px;top:1118px;width:244px}
.recent .side-h{color:#555}
.rp{display:flex;gap:12px;margin-top:16px;height:66px}
.rp .thumb{width:66px;height:66px;background:#8a8a8a;flex:none}
.rp .thumb.face{background:linear-gradient(180deg,#cdd6dc,#8a949a)}
.rp p{font-size:11.5px;line-height:16px;color:#888}
.rp b{display:block;font-size:11px;color:#222;font-weight:600;margin-top:4px}
.portfolio{left:864px;top:1413px;width:244px}
.portfolio .side-h{color:#555}
.grid{display:grid;grid-template-columns:repeat(3,78px);grid-auto-rows:64px;gap:4px;margin-top:14px}
.grid div{background:#8a8a8a}

/* comments */
.comments{left:78px;top:1448px;width:762px}
.comments h2{font-family:"Raleway",sans-serif;font-weight:700;font-size:14px;line-height:20px}
.cm{display:flex;gap:12px;margin-top:10px}
.cm .av{width:66px;height:66px;flex:none;background:#8a8a8a}
.cm .av.warm{background:linear-gradient(180deg,#c8a98d,#7e6554)}
.cm .av.blank{background:#d8d8d8}
.cm h4{font-weight:700;font-size:12.5px;line-height:16px}
.cm .date{font-size:11px;line-height:15px}
.cm .date em{font-style:normal;color:var(--red)}
.cm p{font-size:11.5px;line-height:16px;margin-top:3px}
.cm.reply{margin-left:86px}

/* leave comment */
.blue-line{left:0;top:1860px;width:1200px;height:10px;background:linear-gradient(180deg,#1f6fd0,#5aa0e8)}
.form{left:78px;top:1880px;width:510px}
.form h2{font-family:"Oswald",sans-serif;font-weight:700;font-size:15px;line-height:22px}
.field{width:328px;height:35px;border:1px solid #cfcfcf;background:#fff;margin-top:17px;padding:8px;font-size:11px;color:#333}
.field.msg{width:504px;height:161px}
.submit{left:78px;top:2255px;width:127px;height:29px;background:var(--red);color:#fff;font-family:"Oswald",sans-serif;font-weight:500;font-size:20px;line-height:29px;text-align:center}
.form-photo{left:614px;top:1868px;width:492px;height:368px;background:linear-gradient(180deg,#3a3a3a 0%,#7d7d7d 40%,#2b2b2b 100%);box-shadow:0 6px 16px rgba(0,0,0,.35)}
.dots{left:786px;top:2248px;display:flex;gap:6px}
.dots i{width:11px;height:11px;border-radius:50%;background:#777;display:block}
.dots i:first-child{background:var(--blue)}

/* subscribe */
.sub-photo{left:0;top:2288px;width:1200px;height:580px;background:linear-gradient(180deg,#7a7a7a 0%,#4a4a4a 35%,#222 65%,#1d1d1d 100%)}
.sub-icon{left:584px;top:2398px}
.sub-title{left:0;top:2428px;width:1200px;text-align:center;color:#fff;font-family:"Raleway",sans-serif;font-weight:600;font-size:22px;line-height:32px}
.sub-input{left:338px;top:2492px;width:403px;height:41px;background:#fff;font-family:"Raleway",sans-serif;font-size:9.5px;letter-spacing:1px;color:#777;padding:13px 22px}
.sub-btn{left:747px;top:2492px;width:113px;height:41px;background:var(--teal);color:#fff;font-family:"Raleway",sans-serif;font-weight:700;font-size:9.5px;letter-spacing:1px;display:flex;align-items:center;justify-content:center}

.card{top:2703px;width:248px;height:144px;background:#fff;border:2px solid #ccc;text-align:center;padding-top:28px}
.card .ic{height:16px;display:flex;justify-content:center}
.card h5{font-family:"Raleway",sans-serif;font-weight:600;font-size:10px;letter-spacing:2px;color:#555;margin-top:6px}
.card hr{width:44px;border:0;border-top:2px solid var(--teal);margin:12px auto 14px}
.card p{font-size:10.5px;color:#888}

/* footer */
.footer{left:0;top:2858px;width:1200px;height:212px;background:linear-gradient(180deg,#1d1d1d 0%,#1b4f9c 45%,#d8262a 100%)}
.socials{left:350px;top:2929px;display:flex;gap:22px}
.socials i{width:44px;height:44px;border-radius:50%;border:2px solid rgba(255,255,255,.35);display:block}
.foot-brand{left:20px;top:3010px;font-family:"Raleway",sans-serif;font-weight:700;font-size:30px;color:#2a86f0;letter-spacing:1px;line-height:36px}
</style>
</head>
<body>

<!-- hero -->
<div class="abs hero-photo" role="img" aria-label="Black and white photo of large baobab trees in the bush"></div>
<div class="abs nav-bar"></div>
<div class="abs brand"><span class="brand-dot"></span>KPL CONSTRUCTION</div>
<nav class="abs nav"><a class="active">HOME</a><a>GALLERY</a><a>TOP</a><a>BLOG</a><a>CONTAKT</a></nav>
<div class="abs cart">CART
  <span class="cart-ring"><svg width="18" height="16" viewBox="0 0 18 16"><path d="M1 2h3l2 9h9l2-7H5" fill="none" stroke="#222" stroke-width="1.6"/><circle cx="7" cy="14" r="1.3" fill="#222"/><circle cx="14" cy="14" r="1.3" fill="#222"/></svg></span>
</div>
<div class="abs hero-title">KPL<br>CONSTRUCTION</div>
<div class="abs hero-sub">We are a Construction Company based in the Okavango Delta and specialize in Lodge building.</div>
<div class="abs btn-start">GET STARTED</div>

<!-- post -->
<div class="abs dark-band"></div>
<h1 class="abs page-title">Single Post View</h1>

<div class="abs date-badge"><div class="top">10<br>JUL</div><div class="year">2019</div></div>

<div class="abs slider">
  <div class="abs slide-photo" role="img" aria-label="Sepia photo of a lone oak tree in an open field beside a row of trees"></div>
  <div class="abs slide-caption">
    <h3>Lonely Oak Tree</h3>
    <p>Nullam pretium auctor mauris ut consequat. Etiam hendrerit iaculis mattis. Proin tincidunt gravida augue in tempor. Proin blandit, elit a consectetur tincidunt, velit quam tristique risus, eget ultrices lorem dui id velit.</p>
  </div>
  <svg class="abs slide-arrow" style="left:4px" viewBox="0 0 20 28"><path d="M14 4 5 14l9 10" fill="none" stroke="#333" stroke-width="3"/></svg>
  <svg class="abs slide-arrow" style="right:4px" viewBox="0 0 20 28"><path d="M6 4l9 10-9 10" fill="none" stroke="#333" stroke-width="3"/></svg>
</div>

<div class="abs meta">
  <span class="author"><svg width="12" height="12" viewBox="0 0 12 12"><circle cx="6" cy="3.5" r="2.8" fill="#bbb"/><path d="M1 12c0-3 2.2-5 5-5s5 2 5 5z" fill="#bbb"/></svg>Tom Reed</span>
  <span><svg width="13" height="12" viewBox="0 0 13 12"><path d="M1 1h6l5 5-5 5-5-5V1z" fill="#bbb"/></svg></span>
  <span><svg width="13" height="12" viewBox="0 0 13 12"><path d="M1 1h11v7H5l-3 3V8H1z" fill="none" stroke="#bbb" stroke-width="1.4"/></svg></span>
  <span><svg width="13" height="12" viewBox="0 0 13 12"><path d="M6.5 11 1.5 6a3 3 0 0 1 5-3.5A3 3 0 0 1 11.5 6z" fill="#bbb"/></svg></span>
</div>

<article class="abs post">
  <h1>SINGLE CLEAN POST</h1>
  <p class="lead">Lorem ipsum dolor sit amet, consectetur adipiscing elit. Proin vel lectus ut mauris convallis lacinia dapibus sit amet neque. Praesent scelerisque tellus sit amet ante suscip aliquet magna fringilla. Nullam a purus ut justo consectetur imperdiet. Proin vel lectus ut mauris convallis lacinia dapibus sit amet neque.</p>
  <div class="body">
    <p>Nulla bibendum diam nec tortor ullamcorper sed dapibus sem posuere. Donec nunc sem, consequat ut gravida et, mollis interdum augue. Duis mollis viverra leo, quis rhoncus magna fringilla eget. Phasellus ut ornare orci. Fusce tempor, neque pretium vulputate vehicula, ligula odio convallis mauris, laoreet vehicula dolor odio nec augue. Donec fringilla nisi eget felis sollicitudin pulvinar. Quisque et lorem vel libero elementum eleifend eget vitae tortor. Sed blandit pellentesque tellus vel dignissim.</p>
    <p>Nulla odio ante, rhoncus eu feugiat id, commodo a odio. Donec rhoncus urna nec magna congue molestie.</p>
    <blockquote>Lorem ipsum dolor sit amet, consectetur adipiscing elit. Proin vel lectus ut mauris convallis lacinia dapibus sit amet neque. Praesent scelerisque tellus sit amet ante suscip aliquet magna fringilla. Nullam a purus ut justo consectetur imperdiet. Proin vel lectus ut mauris convallis lacinia dapibus sit amet neque. Donec fringilla nisi eget felis sollicitudin pulvinar.</blockquote>
    <p>Nulla bibendum diam nec tortor ullamcorper sed dapibus sem posuere. Donec nunc sem, consequat ut gravida et, mollis interdum augue. Duis mollis viverra leo, quis rhoncus magna fringilla eget. Phasellus ut ornare orci. Fusce tempor, neque pretium vulputate vehicula, ligula odio convallis mauris, laoreet vehicula dolor odio nec augue. Donec fringilla nisi eget felis sollicitudin pulvinar. Quisque et lorem vel libero elementum eleifend eget vitae tortor. Sed blandit pellentesque tellus vel dignissim.</p>
  </div>
</article>
<div class="abs rule"></div>

<aside class="abs sidebar">
  <div class="side-h">ABOUT THE BLOG</div>
  <p class="side-about">Lorem ipsum dolor sit amet, consectetur adipiscing elit. Proin vel lectus ut mauris convallis lacinia dapibus sit amet neque. Praesent scelerisque tellus sit amet ante suscip aliquet magna fringilla. Nullam a purus ut justo consectetur imperdiet.</p>
  <div class="side-h" style="margin-top:24px">CATEGORIES</div>
  <ul class="cats">
    <li><i></i>Illustration Design (10)</li>
    <li><i></i>Web Design and Development (5)</li>
    <li><i></i>Branding Design (15)</li>
    <li><i></i>Graphic Design(6)</li>
    <li><i></i>Video motion Design (20)</li>
    <li style="border:0"><i></i>Photography (5)</li>
  </ul>
</aside>

<div class="abs recent">
  <div class="side-h">RECENT POST</div>
  <div class="rp"><div class="thumb face" role="img" aria-label="Portrait photo of the post author"></div><div><p>Lorem ipsum dolor sit amet, consectetur adipiscing elit.</p><b>July 10, 2014</b></div></div>
  <div class="rp"><div class="thumb" role="img" aria-label="Project photo"></div><div><p>Lorem ipsum dolor sit amet, consectetur adipiscing elit.</p><b>July 10, 2014</b></div></div>
  <div class="rp"><div class="thumb" role="img" aria-label="Project photo"></div><div><p>Lorem ipsum dolor sit amet, consectetur adipiscing elit.</p><b>July 10, 2014</b></div></div>
</div>

<div class="abs portfolio">
  <div class="side-h">RECENT PORTFOLIO</div>
  <div class="grid" role="img" aria-label="Grid of six project photos"><div></div><div></div><div></div><div></div><div></div><div></div></div>
</div>

<section class="abs comments">
  <h2>4 Comments</h2>
  <div class="cm"><div class="av warm" role="img" aria-label="Commenter photo"></div><div><h4>Lena Marsh</h4><div class="date">July 10, 2014 - <em>Reply</em></div><p>Lorem ipsum dolor sit amet, consectetur adipiscing elit. Proin vel lectus ut mauris convallis lacinia dapibus sit amet neque. Praesent scelerisque tellus sit amet ante suscip aliquet magna fringilla.</p></div></div>
  <div class="cm reply" style="margin-top:12px"><div class="av" role="img" aria-label="Commenter photo"></div><div><h4>Tom Reed</h4><div class="date">July 10, 2014</div><p>Lorem ipsum dolor sit amet, consectetur adipiscing elit. Proin vel lectus ut mauris convallis lacinia dapibus sit amet neque.</p></div></div>
  <div class="cm reply"><div class="av blank" role="img" aria-label="Default avatar placeholder"></div><div><h4>Ivo Hart</h4><div class="date">July 10, 2014</div><p>Thank's you!!!</p></div></div>
  <div class="cm" style="margin-top:44px"><div class="av" role="img" aria-label="Commenter photo"></div><div><h4>Owen Clay</h4><div class="date">July 10, 2014 - <em>Reply</em></div><p>Lorem ipsum dolor sit amet, consectetur adipiscing elit. Proin vel lectus ut mauris convallis lacinia dapibus sit amet neque. Praesent scelerisque tellus sit amet ante suscip aliquet magna fringilla.</p></div></div>
</section>

<!-- leave comment -->
<div class="abs blue-line"></div>
<form class="abs form">
  <h2>Leave Comment</h2>
  <div class="field">Name*</div>
  <div class="field">Email*</div>
  <div class="field">Website</div>
  <div class="field msg">Message*</div>
</form>
<div class="abs submit">SUBMIT</div>
<div class="abs form-photo" role="img" aria-label="Misty forest with tall trees in fog"></div>
<div class="abs dots"><i></i><i></i><i></i><i></i><i></i><i></i><i></i><i></i><i></i></div>

<!-- subscribe -->
<div class="abs sub-photo" role="img" aria-label="Dark misty forest landscape"></div>
<svg class="abs sub-icon" width="30" height="26" viewBox="0 0 30 26"><path d="M2 12 28 2l-6 22-7-8-5 5v-7z" fill="none" stroke="#fff" stroke-width="2" stroke-linejoin="round"/><path d="M15 16 28 2" stroke="#fff" stroke-width="2"/></svg>
<h2 class="abs sub-title">Subscribe to receive updates!</h2>
<div class="abs sub-input">ENTER EMAIL ADDRESS...</div>
<div class="abs sub-btn">SUBSCRIBE</div>

<div class="abs card" style="left:203px">
  <div class="ic"><svg width="14" height="14" viewBox="0 0 14 14"><rect x="1" y="6" width="3" height="7" fill="#4f9a98"/><rect x="5.5" y="2" width="3" height="11" fill="#4f9a98"/><rect x="10" y="4" width="3" height="9" fill="#4f9a98"/></svg></div>
  <h5>ADDRESS</h5><hr><p>48 Delta Road, Maun BW</p>
</div>
<div class="abs card" style="left:475px">
  <div class="ic"><svg width="16" height="12" viewBox="0 0 16 12"><rect x="1" y="1" width="14" height="10" fill="#4f9a98"/><path d="M1 1l7 6 7-6" fill="none" stroke="#fff" stroke-width="1.2"/></svg></div>
  <h5>EMAIL</h5><hr><p>hello@kpl.construction</p>
</div>
<div class="abs card" style="left:745px">
  <div class="ic"><svg width="10" height="15" viewBox="0 0 10 15"><rect x="1" y="1" width="8" height="13" rx="1.5" fill="none" stroke="#4f9a98" stroke-width="1.6"/><circle cx="5" cy="11.5" r="1" fill="#4f9a98"/></svg></div>
  <h5>PHONE</h5><hr><p>+1 (555) 410-2276</p>
</div>

<!-- footer -->
<div class="abs footer"></div>
<div class="abs socials" aria-label="Social links"><i></i><i></i><i></i><i></i><i></i><i></i><i></i><i></i></div>
<div class="abs foot-brand">KPL CONSTRUCTION</div>

</body>
</html>
```